RV7 - Rapid Vigil Field Operations Suite

I need an introductory website for RV7 which describes the features of the product and the ease of use of the product. The product is focused on Preparing for an incident using Volunteer and Resource management and then responding to an incident with Incident Management, Team Management, Task Management and Communication Management. Once a situation is handled, the application provides complete reporting on each of the above aspects

Target Market(s)

Local Government entities, specifically the emergency department directors or coordinators

Industry/Entity Type

Government Office

Coding

Coded - Design and coding required

Font styles to use
Sans Serif

Requirements
Must have
• Clear layout with modern images. I want to be able to get a clear understanding of the features of the product and the ease of use. I would like to high light how the application helps in Communication Management, Team Management, Task Management and Incident Managements. Also, how the use of application helps to get an immediate snap shot of how well an incident was handled. I want to highlight how the Dashboard provides a quick look at the Incident(s) being managed
Nice to have
• I would like to in the future add videos to the site. At this point don't have any ideas about nice to have features
Should not have
• traditional designs. I am looking for a slick, modern looking website. Clean design is the key.

```html
<!DOCTYPE html>
<html lang="en">
<head>
<meta charset="utf-8">
<title>RV7 - Rapid Vigil Field Operations Suite</title>
<link href="https://fonts.googleapis.com/css2?family=Roboto:ital,wght@0,300;0,400;0,500;0,700;1,400&display=swap" rel="stylesheet">
<style>
:root{
  --blue:#2c5da8;
  --blue-dark:#254f91;
  --blue-deep:#1f4682;
  --app-blue:#2a4fb5;
  --green:#8dc63f;
  --ink:#1f1f1f;
  --muted:#666;
  --line:#e2e2e2;
  --grey-band:#e9e9e9;
  --white:#fff;
}
*{margin:0;padding:0;box-sizing:border-box}
html,body{width:1200px;height:3000px;overflow:hidden}
body{font-family:'Roboto',sans-serif;color:var(--ink);background:var(--white);position:relative}
section,header,footer{position:absolute;left:0;width:1200px}
.abs{position:absolute}

/* header */
.site-header{top:0;height:100px;background:var(--white)}
.brand{left:100px;top:22px;display:flex;align-items:center;gap:14px}
.brand-mark{width:52px;height:52px;background:var(--blue);border-radius:6px}
.brand-name{font-size:40px;font-weight:400;color:var(--ink);letter-spacing:1px}
.main-nav{right:98px;top:38px;display:flex;gap:44px;font-size:16px;text-transform:uppercase}
.main-nav a{color:var(--ink);text-decoration:none;padding-bottom:18px}
.main-nav a.active{color:var(--blue);border-bottom:2px solid var(--blue)}

/* hero */
.hero{top:100px;height:565px;overflow:hidden}
.hero-photo{position:absolute;inset:0;background:
  radial-gradient(ellipse 260px 200px at 560px 420px,rgba(240,242,244,.85),rgba(240,242,244,0) 70%),
  radial-gradient(ellipse 300px 260px at 1050px 430px,rgba(250,250,252,.7),rgba(250,250,252,0) 70%),
  radial-gradient(ellipse 380px 420px at 180px 200px,rgba(70,76,84,.9),rgba(70,76,84,0) 75%),
  radial-gradient(ellipse 360px 460px at 1000px 150px,rgba(60,62,66,.95),rgba(60,62,66,0) 75%),
  radial-gradient(ellipse 200px 140px at 620px 180px,rgba(196,160,140,.55),rgba(196,160,140,0) 70%),
  linear-gradient(180deg,#8e969c 0%,#a9afb3 55%,#c4c7c9 100%)}
.hero-shade{position:absolute;inset:0;background:rgba(20,24,30,.18)}
.hero-title{top:218px;width:100%;text-align:center;color:var(--white);font-size:58px;font-weight:700;text-shadow:0 2px 6px rgba(0,0,0,.35)}
.hero-sub{top:286px;width:100%;text-align:center;color:var(--white);font-style:italic;font-size:17px;text-shadow:0 1px 3px rgba(0,0,0,.4)}
.hero-dots{top:500px;left:564px;display:flex;gap:6px}
.hero-dots span{width:16px;height:16px;border-radius:50%;background:var(--white)}
.hero-dots span.off{background:transparent;border:2px solid var(--white)}

/* intro */
.intro{top:665px;height:610px}
.intro-title{top:50px;left:150px;width:900px;text-align:center;font-size:30px;font-weight:400;line-height:40px;text-transform:uppercase}
.intro-sub{top:132px;left:200px;width:800px;text-align:center;font-size:20px;color:var(--muted);line-height:28px}
.role-card{top:301px;width:308px;height:248px;border:1px solid var(--line);text-align:center}
.role-icon{position:absolute;left:90px;top:-68px;width:128px;height:128px;border-radius:50%;background:var(--blue);border:6px solid #dfe6f1;display:flex;align-items:center;justify-content:center}
.role-title{margin-top:74px;font-size:19px;font-weight:500;text-transform:uppercase}
.role-text{margin:14px 24px 0;font-size:12.5px;color:var(--muted);line-height:23px}
.read-more{font-size:13px;font-weight:700;color:var(--green);text-transform:uppercase;display:inline-flex;align-items:center;gap:6px}
.role-card .read-more{margin-top:22px}
.dot-arrow{width:13px;height:13px}

/* featured */
.featured{top:1275px;height:487px;background:
  linear-gradient(120deg,rgba(255,255,255,0) 30%,rgba(255,255,255,.07) 45%,rgba(255,255,255,0) 60%),
  linear-gradient(135deg,var(--blue) 0%,#3467b4 50%,var(--blue-dark) 100%)}
.featured-title{top:34px;width:100%;text-align:center;color:var(--white);font-size:28px;font-weight:500;text-transform:uppercase}
.slider-arrows{top:46px;right:100px;display:flex;gap:4px}
.slider-arrows span{width:20px;height:20px;background:#111;display:flex;align-items:center;justify-content:center}
.service-card{top:110px;width:312px;height:300px;background:var(--white)}
.service-photo{height:166px;margin:4px 4px 0}
.photo-charts{background:
  radial-gradient(ellipse 90px 60px at 150px 90px,rgba(255,255,255,.9),rgba(255,255,255,0) 70%),
  radial-gradient(ellipse 120px 80px at 60px 40px,rgba(232,214,200,.8),rgba(232,214,200,0) 70%),
  linear-gradient(160deg,#e8f1f8 0%,#9cc4e4 45%,#4f8fca 70%,#dde9f3 100%)}
.photo-desk{background:
  radial-gradient(ellipse 70px 50px at 70px 50px,rgba(245,245,245,.9),rgba(245,245,245,0) 70%),
  radial-gradient(ellipse 80px 50px at 220px 110px,rgba(240,240,240,.85),rgba(240,240,240,0) 70%),
  radial-gradient(ellipse 60px 40px at 160px 70px,rgba(60,70,80,.6),rgba(60,70,80,0) 70%),
  linear-gradient(135deg,#9b8468,#c8b496 50%,#8f7a60)}
.photo-screen{background:
  radial-gradient(ellipse 110px 60px at 220px 50px,rgba(120,160,210,.8),rgba(120,160,210,0) 70%),
  radial-gradient(ellipse 90px 60px at 110px 120px,rgba(226,196,176,.7),rgba(226,196,176,0) 70%),
  linear-gradient(135deg,#2f3237,#6b7078 50%,#b8bcc1)}
.service-title{margin:14px 16px 0;font-size:16px;font-weight:500;text-transform:uppercase}
.service-text{margin:10px 16px 0;font-size:12px;color:var(--muted);line-height:19px}
.service-card .read-more{margin:14px 16px 0;text-transform:none;font-size:14px;font-weight:500}

/* volunteer */
.volunteer{top:1762px;height:583px;background:var(--grey-band)}
.section-title{width:100%;text-align:center;font-size:30px;font-weight:700;text-transform:uppercase}
.section-title em{font-style:normal;color:var(--green)}
.volunteer .section-title{top:42px}
.feature-list{top:122px;left:100px;width:300px;list-style:none;font-size:12px;line-height:15px}
.feature-list>li{position:relative;padding-left:18px;margin-bottom:11px}
.feature-list>li::before,.sub-list li::before{content:"";position:absolute;left:2px;top:3px;width:8px;height:5px;border-left:2px solid var(--green);border-bottom:2px solid var(--green);transform:rotate(-45deg)}
.sub-list{list-style:none;margin-top:2px}
.sub-list li{position:relative;padding-left:30px;line-height:14px}
.sub-list li::before{left:14px;border-color:var(--ink)}
.screens-frame{top:128px;left:430px;width:680px;height:384px;background:var(--white);border:1px solid #d8d8d8;box-shadow:0 1px 3px rgba(0,0,0,.08)}
.screens-shot{position:absolute;left:20px;top:20px;width:640px;height:340px;background:#e6e6e6;overflow:hidden;font-size:7px;color:#333}

/* app screens */
.app-screen{position:absolute;top:0;height:340px;width:186px;background:#f1f1f1;overflow:hidden}
.status-bar{height:8px;background:#1d3d99}
.app-bar{height:26px;background:var(--app-blue);color:#fff;display:flex;align-items:center;padding:0 8px;gap:8px;font-size:8px}
.app-bar .title{flex:1}
.bar-icon{width:8px;height:8px;border:1.5px solid #fff;border-radius:2px}
.drawer{position:absolute;left:0;top:8px;width:144px;bottom:0;background:var(--app-blue);color:#fff}
.drawer-head{height:56px;padding:10px 10px 0;border-bottom:1px solid rgba(255,255,255,.2)}
.avatar{width:18px;height:18px;border-radius:50%;background:#f0c83a;border:2px solid #fff}
.drawer-name{font-size:8px;font-weight:500;margin-top:3px}
.drawer-role{font-size:7px;opacity:.8}
.drawer-menu{list-style:none;font-size:6.5px}
.drawer-menu li{height:16px;display:flex;align-items:center;gap:8px;padding-left:10px}
.drawer-menu li::before{content:"";width:5px;height:5px;background:rgba(255,255,255,.7);border-radius:1px}
.drawer-menu li.on{background:rgba(0,0,0,.15)}
.dim{position:absolute;left:144px;top:8px;right:0;bottom:0;background:#8c8c8c}
.note{margin:8px 6px 0;background:#fff;border-radius:2px;box-shadow:0 1px 2px rgba(0,0,0,.2);padding:4px 5px;position:relative}
.note b{display:block;font-weight:400;font-size:6.5px}
.note span{font-size:5.5px;color:#777}
.note i{position:absolute;right:5px;top:4px;font-style:normal;font-size:5px;color:#999}
.task{margin:7px 5px 0;background:#fff;border-top:2px solid var(--app-blue);box-shadow:0 1px 2px rgba(0,0,0,.2);padding:4px 5px;height:74px;position:relative}
.task b{display:block;font-weight:400;font-size:7px}
.task .kind{font-size:5.5px;color:#777}
.task .addr{font-size:5.5px;margin-top:3px;display:flex;gap:3px;align-items:center}
.task .addr::before{content:"";width:4px;height:4px;border-radius:50%;background:#e04848}
.task .eta{font-size:9px;margin-top:5px;display:flex;align-items:center;gap:3px}
.task .eta::before{content:"";width:7px;height:7px;border:1.2px solid #e04848;border-radius:50%}
.task .date{position:absolute;right:5px;bottom:4px;font-size:5px;color:#888}
.task .flag{position:absolute;right:5px;top:5px;width:0;height:0;border-left:4px solid transparent;border-right:4px solid transparent;border-bottom:7px solid #e0a020}
.task .flag.ok{border-bottom-color:#3a9a3a}

/* clients */
.clients{top:2345px;height:317px}
.clients .section-title{top:44px}
.clients-sub{top:96px;width:100%;text-align:center;font-size:16px;color:var(--muted)}
.client-box{top:167px;width:154px;height:96px;border:1px solid var(--line);display:flex;align-items:center;justify-content:center;gap:8px;font-size:15px;font-weight:500;color:var(--blue)}
.client-dot{width:14px;height:14px;border-radius:50%;background:var(--blue)}
.client-arrow{top:202px}

/* footer */
.site-footer{top:2662px;height:338px;background:var(--blue);color:var(--white)}
.foot-col{top:50px}
.foot-col h4{font-size:14px;font-weight:500;text-transform:uppercase;margin-bottom:18px}
.foot-col ul{list-style:none;font-size:12px;line-height:27.5px}
.foot-col p{font-size:12px;line-height:19px}
.news-input{margin-top:18px;width:242px;height:40px;background:var(--white);color:#888;font-size:12px;padding:12px 12px}
.news-btn{margin-top:22px;width:92px;height:38px;background:#1e1e1e;font-size:12px;display:flex;align-items:center;justify-content:center;text-transform:uppercase}
.contact-line{display:flex;align-items:center;gap:10px;font-size:12px;margin-top:14px}
.foot-bar{position:absolute;left:0;top:270px;width:1200px;height:68px;background:var(--blue-deep);font-size:11px}
.copyright{left:100px;top:28px}
.social{left:776px;top:28px;display:flex;gap:14px}
.social b{font-weight:400}
</style>
</head>
<body>

<header class="site-header">
  <div class="brand abs"><span class="brand-mark"></span><span class="brand-name">RV7</span></div>
  <nav class="main-nav abs">
    <a class="active">Home</a><a>About Us</a><a>Application</a><a>How it works</a><a>Blog</a><a>Contact Us</a>
  </nav>
</header>

<section class="hero">
  <div class="hero-photo" role="img" aria-label="Photo of business people in suits handing over a tablet at a desk"></div>
  <div class="hero-shade"></div>
  <h1 class="hero-title abs">EMERGENCY - COMMAND, CONTROL</h1>
  <p class="hero-sub abs">RV7 offers a web based and mobile interface&nbsp; to assist the CERT Community</p>
  <div class="hero-dots abs"><span class="off"></span><span></span><span></span><span></span></div>
</section>

<section class="intro">
  <h2 class="intro-title abs">RV7 – Assisting CERT community in emergency command, control and coordination</h2>
  <p class="intro-sub abs">The roles from CERT teams have been created to have access to either the web, mobile or both the interfaces</p>

  <article class="role-card abs" style="left:100px">
    <div class="role-icon"><svg width="58" height="58" viewBox="0 0 58 58" fill="#fff"><circle cx="29" cy="14" r="9"/><path d="M14 38c0-9 7-14 15-14s15 5 15 14z"/><rect x="10" y="36" width="38" height="12" rx="1"/><rect x="4" y="48" width="50" height="4"/></svg></div>
    <h3 class="role-title">Admin</h3>
    <p class="role-text">The roles from CERT teams have been created to have access to either the web, mobile or both the interfaces</p>
    <span class="read-more">Read more <svg class="dot-arrow" viewBox="0 0 14 14"><circle cx="7" cy="7" r="7" fill="#8dc63f"/><path d="M5 4l3 3-3 3" stroke="#fff" stroke-width="2" fill="none"/></svg></span>
  </article>

  <article class="role-card abs" style="left:446px">
    <div class="role-icon"><svg width="58" height="58" viewBox="0 0 58 58" fill="none" stroke="#fff" stroke-width="3"><rect x="12" y="6" width="30" height="44" rx="4"/><path d="M24 44V26a3 3 0 0 1 6 0v8l10 2v14H26z" fill="#fff"/></svg></div>
    <h3 class="role-title">Incident Command</h3>
    <p class="role-text">The roles from CERT teams have been created to have access to either the web, mobile or both the interfaces</p>
    <span class="read-more">Read more <svg class="dot-arrow" viewBox="0 0 14 14"><circle cx="7" cy="7" r="7" fill="#8dc63f"/><path d="M5 4l3 3-3 3" stroke="#fff" stroke-width="2" fill="none"/></svg></span>
  </article>

  <article class="role-card abs" style="left:792px">
    <div class="role-icon"><svg width="58" height="58" viewBox="0 0 58 58"><path d="M29 50L8 29C2 23 4 12 13 10c6-1 11 2 16 8 5-6 10-9 16-8 9 2 11 13 5 19z" fill="#fff"/></svg></div>
    <h3 class="role-title">Volunteers</h3>
    <p class="role-text">The roles from CERT teams have been created to have access to either the web, mobile or both the interfaces</p>
    <span class="read-more">Read more <svg class="dot-arrow" viewBox="0 0 14 14"><circle cx="7" cy="7" r="7" fill="#8dc63f"/><path d="M5 4l3 3-3 3" stroke="#fff" stroke-width="2" fill="none"/></svg></span>
  </article>
</section>

<section class="featured">
  <h2 class="featured-title abs">Featured Services</h2>
  <div class="slider-arrows abs">
    <span><svg width="8" height="10"><path d="M6 1L2 5l4 4" stroke="#fff" stroke-width="2" fill="none"/></svg></span>
    <span><svg width="8" height="10"><path d="M2 1l4 4-4 4" stroke="#fff" stroke-width="2" fill="none"/></svg></span>
  </div>

  <article class="service-card abs" style="left:100px">
    <div class="service-photo photo-charts" role="img" aria-label="Photo of a hand pointing at charts on a tablet"></div>
    <h3 class="service-title">Incident Management</h3>
    <p class="service-text">The product is focused on Preparing for an incident using Volunteer and Resource management</p>
    <span class="read-more">Read more <svg class="dot-arrow" viewBox="0 0 14 14"><circle cx="7" cy="7" r="7" fill="#8dc63f"/><path d="M5 4l3 3-3 3" stroke="#fff" stroke-width="2" fill="none"/></svg></span>
  </article>

  <article class="service-card abs" style="left:444px">
    <div class="service-photo photo-desk" role="img" aria-label="Photo of a team working with laptops and papers on a wooden desk"></div>
    <h3 class="service-title">Team Management</h3>
    <p class="service-text">The product is focused on Preparing for an incident using Volunteer and Resource management</p>
    <span class="read-more">Read more <svg class="dot-arrow" viewBox="0 0 14 14"><circle cx="7" cy="7" r="7" fill="#8dc63f"/><path d="M5 4l3 3-3 3" stroke="#fff" stroke-width="2" fill="none"/></svg></span>
  </article>

  <article class="service-card abs" style="left:788px">
    <div class="service-photo photo-screen" role="img" aria-label="Photo of a finger touching a customer service touch screen"></div>
    <h3 class="service-title">Task Management</h3>
    <p class="service-text">The product is focused on Preparing for an incident using Volunteer and Resource management</p>
    <span class="read-more">Read more <svg class="dot-arrow" viewBox="0 0 14 14"><circle cx="7" cy="7" r="7" fill="#8dc63f"/><path d="M5 4l3 3-3 3" stroke="#fff" stroke-width="2" fill="none"/></svg></span>
  </article>
</section>

<section class="volunteer">
  <h2 class="section-title abs">Volunteer Mobile <em>Screens</em></h2>
  <ul class="feature-list abs">
    <li>Easy system to register volunteers</li>
    <li>Accurate identification of number of CERT Volunteers available to help in an incident</li>
    <li>Efficient Communication mechanism to reach out to the volunteers via SMS</li>
    <li>Rich graphical visualization of Incidents &amp; Damages associated with the incidents</li>
    <li>Easy Management and Tracking of resources associated with
      <ul class="sub-list"><li>Incident</li><li>Team</li><li>Task</li><li>Supplies</li><li>Volunteers</li></ul>
    </li>
    <li>Capture Notes and pictures about situations being handled</li>
    <li>Easy one click notification to teams on the ground and team members on the same task</li>
    <li>One click social media integration with Chirpa, Snapgram and Vinta related to the Incident</li>
  </ul>
  <div class="screens-frame abs">
    <div class="screens-shot">
      <!-- navigation drawer -->
      <div class="app-screen" style="left:0">
        <div class="status-bar"></div>
        <div class="drawer">
          <div class="drawer-head">
            <div class="avatar"></div>
            <div class="drawer-name">Dana Morrow</div>
            <div class="drawer-role">Volunteer</div>
          </div>
          <ul class="drawer-menu">
            <li>Dashboard</li><li class="on">Notifications</li><li>Profile</li><li>TODO List</li><li>Directory</li><li>Help</li><li>Share</li><li>Logout</li>
          </ul>
        </div>
        <div class="dim"></div>
      </div>
      <!-- notifications -->
      <div class="app-screen" style="left:230px;width:190px">
        <div class="status-bar"></div>
        <div class="app-bar"><span class="title">Notifications</span><span class="bar-icon"></span><span class="bar-icon" style="border-radius:50%"></span></div>
        <div class="note"><b>Impending Weather Conditions</b><span>Impending Weather Conditions</span><i>1 day ago</i></div>
        <div class="note"><b>Incoming Storms. Wrap up in 1 hr</b><span>Incoming Storms. Wrap up in 1 hr</span><i>1 day ago</i></div>
      </div>
      <!-- todo list -->
      <div class="app-screen" style="left:454px">
        <div class="status-bar"></div>
        <div class="app-bar"><span class="title">TODO List</span><span class="bar-icon" style="border-radius:50%"></span><span class="bar-icon"></span><span class="bar-icon" style="border-radius:50%"></span></div>
        <div class="task"><span class="flag"></span><b>Gravel Task</b><span class="kind">Supply Distribution</span><div class="addr">12 Harbor Road, Alder Creek</div><div class="eta">23 Min</div><span class="date">Apr 26, 2016 08:26 AM</span></div>
        <div class="task"><span class="flag ok"></span><b>Find damage area</b><span class="kind">Damage Assessment</span><div class="addr">8 Mill Lane, Alder Creek</div><div class="eta">40 Min</div><span class="date">May 15, 2016 07:36 AM</span></div>
        <div class="task"><span class="flag ok"></span><b>Supply Food</b><span class="kind">Supply Distribution</span><div class="addr">47 Birch Street, Alder Creek</div><div class="eta">40 Min</div><span class="date">Jul 11, 2016 07:15 PM</span></div>
      </div>
    </div>
  </div>
</section>

<section class="clients">
  <h2 class="section-title abs">Our <em>Clients</em></h2>
  <p class="clients-sub abs">The roles from CERT teams have been created to have access to either the web, mobile or both the interfaces</p>
  <svg class="client-arrow abs" style="left:56px" width="16" height="28"><path d="M13 2L3 14l10 12" stroke="#bbb" stroke-width="3" fill="none"/></svg>
  <div class="client-box abs" style="left:100px">Veltrosan</div>
  <div class="client-box abs" style="left:268px"><span class="client-dot"></span>Ember Ledger</div>
  <div class="client-box abs" style="left:438px">Kindpath Trust</div>
  <div class="client-box abs" style="left:608px">Oakline Institute</div>
  <div class="client-box abs" style="left:776px"><span class="client-dot"></span>Marrowby</div>
  <div class="client-box abs" style="left:946px"><span class="client-dot"></span>Sollen Training</div>
  <svg class="client-arrow abs" style="left:1130px" width="16" height="28"><path d="M3 2l10 12L3 26" stroke="#bbb" stroke-width="3" fill="none"/></svg>
</section>

<footer class="site-footer">
  <div class="foot-col abs" style="left:100px">
    <h4>Links</h4>
    <ul><li>Home</li><li>About Us</li><li>Application</li><li>How it Works</li><li>Blog</li><li>Contact Us</li></ul>
  </div>
  <div class="foot-col abs" style="left:252px;width:270px">
    <h4>Join our newsletter</h4>
    <p>RV7 offers a web based and mobile interface&nbsp; to assist the CERT Community</p>
    <div class="news-input">Enter Your Email</div>
    <div class="news-btn">Subscribe</div>
  </div>
  <div class="foot-col abs" style="left:590px">
    <h4>Information</h4>
    <ul><li>Terms &amp; Conditions</li><li>Privacy policy</li><li>Disclaimer</li><li>Contact us</li><li>Sitemap</li></ul>
  </div>
  <div class="foot-col abs" style="left:786px">
    <h4>Why us</h4>
    <ul><li>Customers</li><li>Team</li><li>FAQ</li><li>News</li><li>Others</li></ul>
  </div>
  <div class="foot-col abs" style="left:954px;width:200px">
    <h4>Contact info</h4>
    <p>RV7</p>
    <p style="margin-top:8px">Northwake Systems</p>
    <p style="margin-top:8px">Suite 400, Alder Creek, TX</p>
    <div class="contact-line"><svg width="12" height="12" viewBox="0 0 12 12"><path d="M2 1l2.5 0 1 3-1.5 1c.7 1.5 1.5 2.3 3 3l1-1.5 3 1V11C5 11 1 7 1 2z" fill="#fff"/></svg>555-014-2290</div>
    <div class="contact-line"><svg width="12" height="12" viewBox="0 0 12 12"><circle cx="6" cy="6" r="5.5" fill="#fff"/><circle cx="6" cy="6" r="2" fill="#2c5da8"/></svg>hello@northwake-mail.com</div>
  </div>
  <div class="foot-bar">
    <span class="copyright abs">© 2016, RV7. All rights reserved</span>
    <div class="social abs"><span>Connect with our social network :</span><b>Vinta</b><b>Chirpa</b><b>Plusio</b><b>Pinaro</b><b>Linko</b></div>
  </div>
</footer>

</body>
</html>
```